Luxury Real Estate Website, Midwest, United States

We need web design services for a luxury website. We need IDX Integration with our MLS. We want this to be a very simple website with amazing graphics. We want it to link up with our Mailpost account in order to generate leads through a "More Information" Pop up on the main page. We want the main page to be covered with one large graphic that is a rolling slideshow of active listings of $400,000 and up from the IDX Integration. We need this website to give a very exclusive and sleek look. Lots of black is good... I will upload our logos in Black and Silver. We will also need an "About" page that we are going to call "Qeno Info". We want our graphics to be extremely impressive. Keep in mind, we are a company in the Midwest of the United States, and our real estate has a different look than homes in California or Florida. We need graphics that are realistic for the Midwest, yet still high-end.
Target Market(s)
Luxury Homeowners in the Midwest United States. The graphics needs to be pristine.
Industry/Entity Type
Real Estate
Coding
Coded - Design and coding required
Number of Pages Required
3 page
Requirements
Must have
- Large graphics with IDX Integration. The photos of real estate need to represent real estate that is common in the Midwest, United States. We also need Mailpost integration. We need a pop up that is titled "My Free Market Analysis" that makes them fill out a contact form asking for Full Name, Email Address, Phone Number and Address. This needs to be a pop up on the front page and will integrate with our Mailpost account. We also need a page called "About Qe No Home". And another page where clients can download informational PDFs. The main component needs to be a front page search engine connected with the IDX to access active listings from our MLS. I attached our logos and a sample front page of a website. I would love for ours to look similar.
Nice to have
- Lake House photos on midwest lakes are a plus.
Should not have
- Should not have clutter. This website needs to be clean, luxurious and exclusive.

```html
<!DOCTYPE html>
<html lang="en">
<head>
<meta charset="utf-8">
<title>Oakmere Realty Group — Luxury Real Estate</title>
<link rel="stylesheet" href="https://fonts.googleapis.com/css2?family=Montserrat:wght@400;500;600;700;800&family=Open+Sans:wght@400;600;700&display=swap">
<style>
:root{
  --ink:#1d1d1d;
  --ink-soft:#444;
  --muted:#6b6b6b;
  --white:#ffffff;
  --panel:#f3f3f3;
  --line:#d8d8d8;
  --pale-blue:#cbd8e8;
  --overlay:rgba(20,20,20,.82);
  --sky:#3d6fc4;
  --grass:#4f8a2e;
  --brick:#8a4a35;
}
*{box-sizing:border-box;margin:0;padding:0}
html,body{width:1200px;height:3468px;overflow:hidden}
body{position:relative;background:var(--white);color:var(--ink);font-family:"Open Sans",Arial,sans-serif}
.abs{position:absolute}
.photo{position:absolute}
.head-font{font-family:"Montserrat",Arial,sans-serif}

/* hero */
.hero{left:0;top:0;width:1200px;height:617px;background:linear-gradient(180deg,#1f4fb0 0%,#4d82d6 30%,#9fbde0 50%,#4f8a3a 62%,#6a8e74 72%,#3c5f6e 100%)}
.brand{position:absolute;font-family:"Montserrat",Arial,sans-serif;font-weight:500;letter-spacing:2px;line-height:1.1}
.brand--top{left:132px;top:34px;color:var(--white);font-size:30px}
.brand small{display:block;font-size:12px;letter-spacing:4px;margin-top:4px}
.call{position:absolute;left:898px;top:20px;color:var(--white);font-size:12px;display:flex;align-items:center;gap:8px}
.call b{margin-left:14px;font-weight:600}
.nav{position:absolute;left:572px;top:48px;display:flex;gap:30px;font-size:13px;color:var(--white)}
.nav a{color:inherit;text-decoration:none;padding:4px 10px}
.nav a.is-active{border:1px solid var(--white)}
.hero-title{position:absolute;left:169px;top:248px;color:var(--white);font-family:"Montserrat",Arial,sans-serif;font-weight:700;font-size:44px;line-height:48px;letter-spacing:1px;text-shadow:0 2px 6px rgba(0,0,0,.35)}
.search{position:absolute;left:171px;top:379px;width:434px;height:48px;display:flex;background:var(--white);font-size:12px;color:var(--ink-soft)}
.search .field{flex:1;padding:0 18px;display:flex;align-items:center}
.search .type{width:90px;border-left:1px solid var(--line);display:flex;align-items:center;justify-content:center;gap:14px}
.search .go{width:50px;background:var(--ink);display:flex;align-items:center;justify-content:center}
.dots{position:absolute;left:580px;top:541px;display:flex;gap:10px;align-items:center}
.dots i{width:7px;height:7px;border-radius:50%;background:var(--white);display:block}
.dots i.on{width:12px;height:12px;background:transparent;border:2px solid var(--white)}

/* welcome */
.welcome-photo{left:132px;top:665px;width:312px;height:205px;background:linear-gradient(180deg,#9ec3e8 0%,#d6e3ef 35%,#8e4a36 50%,#7a3e2c 70%,#4c7a2e 85%,#3d6626 100%)}
.eyebrow{font-family:"Montserrat",Arial,sans-serif;font-weight:600;font-size:13px;letter-spacing:1px}
.welcome-title{left:497px;top:712px;font-family:"Montserrat",Arial,sans-serif;font-weight:600;font-size:29px;line-height:36px;letter-spacing:1px}
.vrule{left:689px;top:672px;width:1px;height:192px;background:var(--line)}
.body-copy{font-size:11.5px;line-height:17px;color:var(--ink-soft)}
.btn{position:absolute;background:var(--ink);color:var(--white);font-family:"Montserrat",Arial,sans-serif;font-weight:700;font-size:10.5px;letter-spacing:.5px;display:flex;align-items:center;justify-content:center}

/* featured */
.featured{left:0;top:935px;width:1200px;height:457px;background:var(--panel)}
.section-title{font-family:"Montserrat",Arial,sans-serif;font-weight:700;font-size:26px;letter-spacing:.5px}
.feat-card{position:absolute;top:1098px;width:222px;text-align:center}
.feat-card .img{height:161px}
.feat-card .city{margin-top:22px;font-size:13px;color:var(--ink-soft)}
.feat-card .price{margin-top:6px;font-family:"Montserrat",Arial,sans-serif;font-weight:700;font-size:16px}
.feat-sep{position:absolute;top:1270px;width:1px;height:58px;background:var(--line)}

/* list of homes */
.list-intro{left:0;top:1392px;width:300px;height:240px;background:var(--pale-blue);text-align:center;padding-top:78px}
.list-intro h3{font-family:"Montserrat",Arial,sans-serif;font-weight:700;font-size:19px;letter-spacing:.5px;color:#2b2b2b}
.list-intro p{margin:12px auto 0;width:170px;font-size:11px;line-height:16px;color:var(--ink-soft)}
.home-card{position:absolute;width:300px;height:240px;overflow:hidden}
.home-card .price-tag{position:absolute;right:4px;top:12px;background:var(--white);color:var(--ink);font-family:"Montserrat",Arial,sans-serif;font-weight:700;font-size:11px;padding:4px 7px}
.home-card .name{position:absolute;left:18px;bottom:36px;color:var(--white);font-family:"Montserrat",Arial,sans-serif;font-weight:700;font-size:12.5px;text-shadow:0 1px 3px rgba(0,0,0,.6)}
.home-card .stats{position:absolute;left:0;bottom:0;width:100%;height:28px;background:rgba(25,25,25,.72);display:flex;justify-content:space-around;align-items:center;color:#e6e6e6;font-size:10px}

/* blog */
.blog-card{position:absolute;top:2045px;width:256px;height:370px;background:#f7f6f5;border:1px solid #e6e6e6}
.blog-card .img{height:168px}
.blog-card h4{margin:30px 30px 0;font-family:"Montserrat",Arial,sans-serif;font-weight:700;font-size:12px;line-height:16px}
.blog-card p{margin:12px 30px 0;font-size:11px;line-height:15px;color:var(--ink-soft)}
.blog-card .btn{left:30px;bottom:32px;width:78px;height:22px;font-size:10px}

/* week banner */
.banner{left:0;top:2529px;width:1200px;height:584px;background:linear-gradient(180deg,#6f9fd6 0%,#b9cfe6 22%,#5d7f4b 45%,#c8bca6 55%,#a79f8c 70%,#3f6f2a 84%,#5c8f3a 100%)}
.week-box{left:698px;top:2620px;width:347px;height:447px;background:var(--overlay);color:var(--white);text-align:center;padding-top:66px}
.week-box h3{font-family:"Montserrat",Arial,sans-serif;font-weight:700;font-size:19px;line-height:27px;letter-spacing:.5px}
.week-box p{margin:20px auto 0;width:240px;font-size:11px;line-height:16px;color:#d9d9d9}
.week-box .amount{margin-top:42px;font-family:"Montserrat",Arial,sans-serif;font-weight:700;font-size:40px}
.week-box .btn{position:static;margin:30px auto 0;width:112px;height:32px;background:var(--white);color:var(--ink);font-size:13px}

/* footer */
.brand--foot{left:132px;top:3202px;color:var(--ink);font-size:36px}
.brand--foot small{font-size:14px;letter-spacing:6px}
.foot-col{position:absolute;top:3150px;font-size:11px;color:var(--ink-soft)}
.foot-col h5{font-family:"Montserrat",Arial,sans-serif;font-weight:700;font-size:12px;color:var(--ink);margin-bottom:22px}
.foot-row{display:flex;gap:12px;align-items:flex-start;line-height:16px;margin-bottom:18px}
.foot-menu li{list-style:none;line-height:18px}
.social{display:flex;align-items:center;gap:12px;margin-bottom:14px}
.social i{width:26px;height:26px;border-radius:50%;background:#2a3f6e;display:block}
.social:nth-child(3) i{background:#2aa3e0}
.social:nth-child(4) i{background:#1e3d7a}
.foot-rule{left:132px;top:3353px;width:936px;height:1px;background:var(--line)}
.copyright{left:132px;top:3411px;font-size:11px;color:var(--ink-soft)}
.partner{left:866px;top:3400px;display:flex;align-items:center;gap:10px;font-family:"Montserrat",Arial,sans-serif;font-weight:600;font-size:26px;color:#3a3a3a}
.partner i{width:40px;height:40px;border-radius:50%;background:#3a3a3a;display:block}
</style>
</head>
<body>

<!-- Hero -->
<section class="hero abs" role="img" aria-label="Brick lake house with a steep roof beside a calm reflecting pond under a blue sky"></section>
<div class="brand brand--top">OAKMERE<small>REALTY GROUP</small></div>
<div class="call">
  <svg width="13" height="13" viewBox="0 0 24 24" fill="#fff"><path d="M6.6 10.8a15.1 15.1 0 0 0 6.6 6.6l2.2-2.2c.3-.3.7-.4 1-.2 1.1.4 2.3.6 3.6.6.6 0 1 .4 1 1V20c0 .6-.4 1-1 1A17 17 0 0 1 3 4c0-.6.4-1 1-1h3.5c.6 0 1 .4 1 1 0 1.3.2 2.5.6 3.6.1.3 0 .7-.2 1z"/></svg>
  Call Us : <b>555.010.2040</b>
</div>
<nav class="nav">
  <a class="is-active">Home</a><a>Qeno Info</a><a>About Qe No Home</a><a>Downloads</a><a>Contact us</a>
</nav>
<h1 class="hero-title">LUXURY<br>REAL ESTATE</h1>
<div class="search">
  <div class="field">Search home by city &amp; State</div>
  <div class="type">Buy
    <svg width="8" height="6" viewBox="0 0 8 6"><path d="M1 1l3 3 3-3" stroke="#444" stroke-width="1.4" fill="none"/></svg>
  </div>
  <div class="go">
    <svg width="16" height="16" viewBox="0 0 24 24"><circle cx="10" cy="10" r="6.5" stroke="#fff" stroke-width="2.6" fill="none"/><path d="M15 15l6 6" stroke="#fff" stroke-width="2.8"/></svg>
  </div>
</div>
<div class="dots"><i></i><i></i><i class="on"></i><i></i><i></i></div>

<!-- Welcome -->
<div class="photo welcome-photo" role="img" aria-label="Large two-storey red brick family home with a green lawn"></div>
<div class="abs eyebrow" style="left:497px;top:682px">WELCOME TO</div>
<h2 class="abs welcome-title">OAKMERE<br>REALTY<br>GROUP</h2>
<div class="abs vrule"></div>
<p class="abs body-copy" style="left:760px;top:684px;width:310px">Sed ut perspiciatis unde omnis iste natus error sit voluptatem accusantium doloremque laudantium, totam rem aperiam, eaque ipsa quae ab illo inventore veritatis et quasi architecto beatae vitae dicta sunt explicabo. Nemo enim ipsam voluptatem quia voluptas sit aspernatur aut</p>
<div class="btn" style="left:762px;top:792px;width:94px;height:30px">READ MORE</div>

<!-- Featured -->
<section class="featured abs"></section>
<div class="abs eyebrow" style="left:132px;top:990px">FEATURED</div>
<h2 class="abs section-title" style="left:132px;top:1012px">LUXURY HOMES</h2>
<div class="btn" style="left:966px;top:1014px;width:102px;height:31px">SHOW MORE</div>

<div class="feat-card" style="left:132px"><div class="img" role="img" aria-label="Stone manor with a curved driveway" style="background:linear-gradient(180deg,#8fb6e0 0%,#c9d6d9 35%,#a08c6e 55%,#6f8a4a 100%)"></div><div class="city">Philadelphia, PA</div><div class="price">$2,350,000</div></div>
<div class="feat-sep" style="left:362px"></div>
<div class="feat-card" style="left:370px"><div class="img" role="img" aria-label="Green and red timber houses on a reflecting lake" style="background:linear-gradient(180deg,#7fb3e6 0%,#a9cfe6 30%,#2f7a4a 50%,#b8342a 62%,#4f8fb0 100%)"></div><div class="city">Toledo, OH</div><div class="price">$1,350,000</div></div>
<div class="feat-sep" style="left:600px"></div>
<div class="feat-card" style="left:608px"><div class="img" role="img" aria-label="Modern brick home lit warmly at dusk" style="background:linear-gradient(180deg,#1b2440 0%,#3a3f5c 35%,#c98a3e 60%,#6b4a2c 85%,#2f2a24 100%)"></div><div class="city">Houston, TX</div><div class="price">$2,350,000</div></div>
<div class="feat-sep" style="left:838px"></div>
<div class="feat-card" style="left:846px"><div class="img" role="img" aria-label="Dark red wooden cottage among tall pines" style="background:linear-gradient(180deg,#8fb0d8 0%,#cfdae6 30%,#5a2a22 55%,#3f5f2a 80%,#4e7a2c 100%)"></div><div class="city">Silver Spring, MD</div><div class="price">$2,350,000</div></div>

<!-- List of homes -->
<div class="abs list-intro"><h3>LIST OF HOMES</h3><p>Sed ut perspiciatis unde omnis iste natus error sit voluptatem</p></div>

<article class="home-card" style="left:300px;top:1392px"><div class="photo" style="inset:0;background:linear-gradient(180deg,#4f6e3a 0%,#7a3a2c 40%,#8e5040 60%,#3d5f27 100%)" role="img" aria-label="Red brick cottage among trees"></div><span class="price-tag">$ 2,350,000</span><span class="name">LOREM IPSUM DOLOR SIT</span><div class="stats"><span>2 Beds</span><span>1 Bathroom</span><span>1 Kitchen</span><span>350ft²</span></div></article>
<article class="home-card" style="left:600px;top:1392px"><div class="photo" style="inset:0;background:linear-gradient(180deg,#6f9ed0 0%,#7e8c8e 40%,#a4342c 60%,#3f5f2a 100%)" role="img" aria-label="Grey lakeside house with red garden"></div><span class="price-tag">$ 2,350,000</span><span class="name">LOREM IPSUM DOLOR SIT</span><div class="stats"><span>2 Beds</span><span>1 Bathroom</span><span>1 Kitchen</span><span>350ft²</span></div></article>
<article class="home-card" style="left:900px;top:1392px"><div class="photo" style="inset:0;background:linear-gradient(180deg,#3f6e2c 0%,#5f83b0 35%,#46638f 55%,#4a7a2a 100%)" role="img" aria-label="Blue clapboard house with double garage"></div><span class="price-tag">$ 2,350,000</span><span class="name">LOREM IPSUM DOLOR SIT</span><div class="stats"><span>2 Beds</span><span>1 Bathroom</span><span>1 Kitchen</span><span>350ft²</span></div></article>

<article class="home-card" style="left:0;top:1632px"><div class="photo" style="inset:0;background:linear-gradient(180deg,#8fb8e6 0%,#b86a3a 40%,#d9d2c6 58%,#4f7fa8 100%)" role="img" aria-label="Waterfront house with a boat dock"></div><span class="price-tag">$ 2,350,000</span><span class="name">LOREM IPSUM DOLOR SIT</span><div class="stats"><span>2 Beds</span><span>1 Bathroom</span><span>1 Kitchen</span><span>350ft²</span></div></article>
<article class="home-card" style="left:300px;top:1632px"><div class="photo" style="inset:0;background:linear-gradient(180deg,#6f9fd8 0%,#a9c3e2 30%,#7a3e30 55%,#4e7a2e 100%)" role="img" aria-label="Brick colonial with tall gables"></div><span class="price-tag">$ 2,350,000</span><span class="name">LOREM IPSUM DOLOR SIT</span><div class="stats"><span>2 Beds</span><span>1 Bathroom</span><span>1 Kitchen</span><span>350ft²</span></div></article>
<article class="home-card" style="left:600px;top:1632px"><div class="photo" style="inset:0;background:linear-gradient(180deg,#6f9fd8 0%,#c9d3dc 30%,#e6e6e6 55%,#4f7a2e 100%)" role="img" aria-label="White colonial house with dark shutters"></div><span class="price-tag">$ 2,350,000</span><span class="name">LOREM IPSUM DOLOR SIT</span><div class="stats"><span>2 Beds</span><span>1 Bathroom</span><span>1 Kitchen</span><span>350ft²</span></div></article>
<article class="home-card" style="left:900px;top:1632px"><div class="photo" style="inset:0;background:linear-gradient(180deg,#7fb0e6 0%,#c8dcee 35%,#a04a34 55%,#5f8a2e 100%)" role="img" aria-label="Red brick ranch house on a wide lawn"></div><span class="price-tag">$ 2,350,000</span><span class="name">LOREM IPSUM DOLOR SIT</span><div class="stats"><span>2 Beds</span><span>1 Bathroom</span><span>1 Kitchen</span><span>350ft²</span></div></article>

<!-- Blog -->
<h2 class="abs" style="left:0;top:1940px;width:1200px;text-align:center;font-family:'Montserrat',Arial,sans-serif;font-weight:700;font-size:19px;letter-spacing:.5px">FROM OUR BLOG</h2>

<article class="blog-card" style="left:178px"><div class="img" role="img" aria-label="Stone and brick estate home at sunset" style="background:linear-gradient(180deg,#8fb6e0 0%,#d6dfe6 30%,#6a4a36 55%,#4f7a2e 100%)"></div><h4>Sed ut perspiciatis unde omnis iste natus error sit</h4><p>Sed ut perspiciatis unde omnis iste n atus error sit voluptatem accusantium doloremque accusantium dolore mque laudantiu totam.</p><div class="btn">READ MORE</div></article>
<article class="blog-card" style="left:472px"><div class="img" role="img" aria-label="Grey shingled house on a green lawn" style="background:linear-gradient(180deg,#7fb0e6 0%,#c9d9e8 35%,#8a96a4 55%,#4f8a2e 100%)"></div><h4>Sed ut perspiciatis unde omnis iste natus error sit</h4><p>Sed ut perspiciatis unde omnis iste n atus error sit voluptatem accusantium doloremque accusantium dolore mque laudantiu totam.</p><div class="btn">READ MORE</div></article>
<article class="blog-card" style="left:767px"><div class="img" role="img" aria-label="White farmhouse with a wraparound porch" style="background:linear-gradient(180deg,#7fb0e6 0%,#d9e2ea 35%,#eeeeee 55%,#4f7a2e 100%)"></div><h4>Sed ut perspiciatis unde omnis iste natus error sit</h4><p>Sed ut perspiciatis unde omnis iste n atus error sit voluptatem accusantium doloremque accusantium dolore mque laudantiu totam.</p><div class="btn">READ MORE</div></article>

<!-- Luxury of the week -->
<section class="banner abs" role="img" aria-label="Beige two-storey house with a garden patio and yellow umbrella among tall trees"></section>
<div class="abs week-box">
  <h3>LUXURY REAL ESTATE<br>OF THE WEEK</h3>
  <p>Sed ut perspiciatis unde omnis iste n atus error sit voluptatem accusantium doloremque accusantium dolore mque laudantiu totam.</p>
  <div class="amount">$ 1,225,00</div>
  <div class="btn">READ MORE</div>
</div>

<!-- Footer -->
<div class="brand brand--foot">OAKMERE<small>REALTY GROUP</small></div>

<div class="foot-col" style="left:502px">
  <h5>CONTACT US</h5>
  <div class="foot-row"><svg width="11" height="14" viewBox="0 0 24 30"><path d="M12 0a10 10 0 0 0-10 10c0 7.5 10 20 10 20s10-12.5 10-20A10 10 0 0 0 12 0zm0 14a4 4 0 1 1 0-8 4 4 0 0 1 0 8z" fill="#333"/></svg><span>14 Larkspur Lane<br>Fairhaven 4812</span></div>
  <div class="foot-row"><svg width="12" height="12" viewBox="0 0 24 24" fill="#333"><path d="M6.6 10.8a15.1 15.1 0 0 0 6.6 6.6l2.2-2.2c.3-.3.7-.4 1-.2 1.1.4 2.3.6 3.6.6.6 0 1 .4 1 1V20c0 .6-.4 1-1 1A17 17 0 0 1 3 4c0-.6.4-1 1-1h3.5c.6 0 1 .4 1 1 0 1.3.2 2.5.6 3.6.1.3 0 .7-.2 1z"/></svg><span>555.010.2040</span></div>
  <div class="foot-row"><svg width="13" height="10" viewBox="0 0 26 20"><rect x="1" y="1" width="24" height="18" fill="#333"/><path d="M1 1l12 10L25 1" stroke="#fff" stroke-width="2" fill="none"/></svg><span>info@oakmere.com</span></div>
</div>

<div class="foot-col" style="left:746px">
  <h5>MENU</h5>
  <ul class="foot-menu"><li>Home</li><li>Qeno Info</li><li>About Qe No Home</li><li>Downloads</li><li>Contact us</li></ul>
</div>

<div class="foot-col" style="left:934px">
  <h5>CONNECT WITH US</h5>
  <div class="social"><i></i>Facelink</div>
  <div class="social"><i></i>Chirper</div>
  <div class="social"><i></i>Worknet</div>
</div>

<div class="abs foot-rule"></div>
<div class="abs copyright">Copyrights @ 2018 All Rights Reserved</div>
<div class="abs partner"><i></i>Mailpost</div>

</body>
</html>
```